Maple Bus Card

i own a building in the bronx ny - its called "Maple 7 on 2 HDFC"i want a classy logo / business card - nothing too religuous but it is like a family there - its a large apartment building - colors i like dark red, black, medium shade of gray also reg business card stuff tel # 914-555-0173 address 4738 Larkwell Ave Bronx NY 10460 Email fijosh@aol.comslogan - " from many we are one "i can send u a picture of the building for the backside

```html
<!DOCTYPE html>
<html lang="en">
<head>
<meta charset="utf-8">
<title>Maple 7 on 2 HDFC – Business Card</title>
<link rel="stylesheet" href="https://fonts.googleapis.com/css2?family=Oswald:wght@500&family=Open+Sans:wght@400;600;700&display=swap">
<style>
  :root {
    --backdrop: #8c5226;
    --card-black: #0d0d0d;
    --gold: #f2b51c;
    --gray: #a9a9a9;
    --gray-light: #c8c8c8;
    --rule: #5a5a5a;
    --brand-red: #c8161d;
    --brick-dark: #4a2620;
    --brick: #7a3b30;
  }
  * { margin: 0; padding: 0; box-sizing: border-box; }
  html, body { width: 1200px; height: 900px; overflow: hidden; }
  body { background: var(--backdrop); position: relative; font-family: "Open Sans", sans-serif; }

  .card { position: absolute; box-shadow: 3px 4px 8px rgba(0,0,0,.45); }

  .card-front {
    left: 330px; top: 90px; width: 555px; height: 345px;
    background: var(--card-black);
    text-align: center;
    color: var(--gray);
  }
  .brand-mark {
    position: absolute; left: 0; right: 0; top: 140px;
    display: flex; justify-content: center; align-items: center; gap: 12px;
    top: 138px;
  }
  .brand-mark { top: 40px; }
  .brand-dot { width: 16px; height: 16px; border-radius: 50%; background: var(--brand-red); }
  .brand-word {
    font-family: "Oswald", sans-serif; font-weight: 500;
    font-size: 44px; letter-spacing: 8px; color: var(--gray);
    line-height: 1;
  }
  .company-name {
    position: absolute; left: 0; right: 0; top: 130px;
    font-family: "Oswald", sans-serif; font-weight: 500;
    font-size: 44px; line-height: 1; color: var(--gold); letter-spacing: 1px;
  }
  .company-type {
    position: absolute; left: 142px; right: 142px; top: 181px;
    display: flex; align-items: center; gap: 10px;
    font-weight: 700; font-size: 17px; color: var(--gray); letter-spacing: 1px;
  }
  .company-type::before, .company-type::after {
    content: ""; flex: 1; height: 1px; background: var(--gray);
  }
  .slogan {
    position: absolute; left: 0; right: 0; top: 214px;
    font-weight: 700; font-size: 15px; letter-spacing: 1.5px; color: var(--gray);
  }
  .divider {
    position: absolute; left: 136px; right: 138px; top: 251px;
    height: 1px; background: var(--rule);
  }
  .contact-line {
    position: absolute; left: 0; right: 0; top: 264px;
    font-size: 16px; color: var(--gray);
  }
  .contact-line .label { color: var(--gold); font-weight: 600; }
  .contact-line .sep { margin: 0 8px; }
  .address {
    position: absolute; left: 0; right: 0; top: 293px;
    font-size: 16px; color: var(--gray);
  }

  .card-back {
    left: 330px; top: 470px; width: 559px; height: 343px;
    background: linear-gradient(180deg, #6e3a30 0%, var(--brick) 45%, var(--brick-dark) 80%, #2f2a2a 100%);
  }
</style>
</head>
<body>
  <section class="card card-front">
    <div class="brand-mark">
      <span class="brand-dot"></span>
      <span class="brand-word">MAPLE</span>
    </div>
    <h1 class="company-name">MAPLE 7 ON 2</h1>
    <div class="company-type">HDFC</div>
    <p class="slogan">FROM MANY WE ARE ONE</p>
    <div class="divider"></div>
    <p class="contact-line"><span class="label">P:</span> 914-555-0173<span class="sep">|</span><span class="label">E:</span> mavreld@quintmail.com</p>
    <p class="address">4738 Larkwell Ave Bronx NY 10460</p>
  </section>

  <section class="card card-back" role="img" aria-label="Photograph of the brick apartment building facade with fire escapes and the red entrance door"></section>
</body>
</html>
```